Business Card Design

An energy company designed around renewable energy and energy storage that focuses on providing its energy at points on the grid that reduce costs and add value to the system.

Industry/Entity Type

Business

Contact Information for Business Card

Gavin Kellerby
Executive Vice President
53 K ST NE
Washington, DC 20019
301-555-0187
gkellerby@tallowmereco.com

```html
<!DOCTYPE html>
<html lang="en">
<head>
<meta charset="utf-8">
<title>Quenvaro Business Card</title>
<link rel="stylesheet" href="https://fonts.googleapis.com/css2?family=Open+Sans:wght@400;600;700&display=swap">
<style>
  :root {
    --backdrop: #2b2725;
    --card: #151515;
    --card-edge: #0c0c0c;
    --ink-white: #f2f2f2;
    --ink-soft: #cfcfcf;
    --ink-grey: #9a9a9a;
    --divider: #3a3a3a;
  }
  * { margin: 0; padding: 0; box-sizing: border-box; }
  html, body {
    width: 1200px; height: 844px; overflow: hidden;
    background: var(--backdrop);
    font-family: "Open Sans", Arial, sans-serif;
  }
  .canvas {
    position: relative; width: 1200px; height: 844px;
    display: flex; align-items: center; justify-content: center; gap: 60px;
  }
  .card {
    position: relative; width: 500px; height: 286px;
    background: var(--card);
    border: 1px solid var(--card-edge);
    box-shadow: 0 10px 30px rgba(0,0,0,.45);
    display: flex; align-items: center;
  }
  .card__brand {
    display: flex; align-items: center; justify-content: center;
    font-weight: 700; letter-spacing: 2px; white-space: nowrap;
  }
  .card--front .card__brand { width: 230px; }
  .card--front .brand-name { color: var(--ink-white); font-size: 26px; }
  .card__divider {
    align-self: center; width: 1px; height: 150px; background: var(--divider);
  }
  .card__details {
    padding-left: 18px; color: var(--ink-soft);
    font-size: 12.5px; line-height: 1.4; white-space: nowrap;
  }
  .details__name { color: var(--ink-white); font-size: 19px; font-weight: 600; line-height: 1.2; }
  .details__title { font-size: 11.5px; margin-bottom: 14px; }
  .details__contact { margin-bottom: 12px; }
  .card--back .card__brand { width: 250px; }
  .card--back .brand-name { color: var(--ink-grey); font-size: 24px; }
  .card--back .card__divider { height: 110px; }
  .back__name {
    padding-left: 16px; color: var(--ink-grey);
    font-size: 20px; font-weight: 700; letter-spacing: 2px; line-height: 1.1;
  }
</style>
</head>
<body>
<main class="canvas">
  <section class="card card--front">
    <div class="card__brand">
      <span class="brand-name">QUENVARO</span>
    </div>
    <div class="card__divider"></div>
    <div class="card__details">
      <p class="details__name">Gavin Kellerby</p>
      <p class="details__title">Executive Vice President</p>
      <div class="details__contact">
        <p>T: 301-555-0187</p>
        <p>E: gkellerby@tallowmereco.com</p>
        <p>W: www.tallowmereco.com</p>
      </div>
      <p>53 K ST NE</p>
      <p>Washington, DC 20019</p>
    </div>
  </section>

  <section class="card card--back">
    <div class="card__brand">
      <span class="brand-name">QUENVARO</span>
    </div>
    <div class="card__divider"></div>
    <div class="back__name">
      <p>GAVIN</p>
      <p>KELLERBY</p>
    </div>
  </section>
</main>
</body>
</html>
```